Redesign of business card for Cedar Ridge Mechanical

We are looking for a new design for our business cards for Cedar Ridge Mechanical. We are a plumbing & HVAC construction company, operating on the West Coast of Canada and USA. Logo attached.
Industry/Entity Type
Construction - Plumbing & HVAC
Contact Information for Business Card
Name, address, phone numbers, email, website address
Look and feel
Each slider illustrates characteristics of the customer's brand and the style your logo design should communicate.

```html
<!DOCTYPE html>
<html lang="en">
<head>
<meta charset="utf-8">
<title>Cedar Ridge Mechanical – Business Card</title>
<link href="https://fonts.googleapis.com/css2?family=Montserrat:wght@400;500;700&display=swap" rel="stylesheet">
<style>
  :root {
    --stage: #2a2a2c;
    --card-white: #ffffff;
    --card-black: #161616;
    --wave-edge: #9a9a9a;
    --ink-dark: #222222;
    --ink-light: #f4f4f4;
  }
  * { margin: 0; padding: 0; box-sizing: border-box; }
  html, body {
    width: 1200px; height: 801px; overflow: hidden;
    background: var(--stage);
    font-family: "Montserrat", sans-serif;
  }
  .stage { position: relative; width: 1200px; height: 801px; }
  .card {
    position: absolute;
    width: 525px; height: 300px;
    border-radius: 20px;
    overflow: hidden;
    background: var(--card-white);
    box-shadow: 0 18px 40px rgba(0,0,0,.45);
  }
  .card--back { left: 50px; top: 120px; }
  .card--front { left: 625px; top: 381px; }

  .card__wave { position: absolute; inset: 0; width: 100%; height: 100%; }

  .contact {
    position: absolute; left: 42px; top: 62px;
    color: var(--ink-light);
  }
  .contact__name { font-weight: 700; font-size: 23px; letter-spacing: 1px; text-transform: uppercase; }
  .contact__role { font-size: 15px; font-weight: 500; margin-top: 2px; }
  .contact__address { font-size: 15px; line-height: 1.35; margin-top: 26px; }
  .contact__list { list-style: none; margin-top: 28px; font-size: 15px; line-height: 1.5; }
  .contact__list li { display: flex; align-items: center; gap: 8px; }
  .contact__icon { width: 13px; height: 13px; flex: none; }

  .brand {
    position: absolute; display: flex; align-items: center; gap: 12px;
    color: var(--ink-dark); font-weight: 700; text-transform: uppercase; letter-spacing: 1.5px;
  }
  .brand__mark { background: var(--ink-dark); flex: none; }
  .card--back .brand {
    left: 345px; width: 160px; top: 92px;
    flex-direction: column; align-items: center; text-align: center;
    font-size: 15px; line-height: 1.35;
  }
  .card--back .brand__mark { width: 30px; height: 30px; }
  .card--front .brand { left: 0; right: 0; top: 128px; justify-content: center; font-size: 26px; }
  .card--front .brand__mark { width: 28px; height: 28px; }
</style>
</head>
<body>
<main class="stage">
  <section class="card card--back" aria-label="Business card back with contact details">
    <svg class="card__wave" viewBox="0 0 525 300" preserveAspectRatio="none" aria-hidden="true">
      <path d="M0,0 H270 C340,80 240,200 310,300 H0 Z" fill="var(--wave-edge)"/>
      <path d="M0,0 H262 C330,80 230,200 300,300 H0 Z" fill="var(--card-black)"/>
    </svg>
    <div class="contact">
      <p class="contact__name">Jonathan Smith</p>
      <p class="contact__role">Manager</p>
      <p class="contact__address">Your address, city<br>state, ZIP 0000</p>
      <ul class="contact__list">
        <li><svg class="contact__icon" viewBox="0 0 16 16"><path fill="currentColor" d="M3 1l3 3-2 2c1 2 3 4 5 5l2-2 3 3-2 3C6 15 1 10 0 4z"/></svg>123-456-2100</li>
        <li><svg class="contact__icon" viewBox="0 0 16 16"><rect x="1" y="3" width="14" height="10" rx="1" fill="currentColor"/><path d="M1 4l7 5 7-5" stroke="var(--card-black)" stroke-width="1.5" fill="none"/></svg>youremail@mailbox.com</li>
        <li><svg class="contact__icon" viewBox="0 0 16 16"><circle cx="8" cy="8" r="7" fill="currentColor"/><path d="M1 8h14M8 1c3 3 3 11 0 14M8 1c-3 3-3 11 0 14" stroke="var(--card-black)" stroke-width="1.2" fill="none"/></svg>www.yourwebsite.com</li>
      </ul>
    </div>
    <div class="brand"><span class="brand__mark"></span><span class="brand__name">Cedar Ridge Mechanical</span></div>
  </section>

  <section class="card card--front" aria-label="Business card front">
    <div class="brand"><span class="brand__mark"></span><span class="brand__name">Cedar Ridge Mechanical</span></div>
  </section>
</main>
</body>
</html>
```